Book cover - Lanterns Along the Winding Quay

Book cover for Ebook (Quillet) and wrap around print cover (Bindwell) (back, front, and spine)

The book title (may slightly change by end of brief):
(MAIN TITLE) 'Lanterns Along the Winding Quay'
(SUB HEADING) 'A Practical Seasonal Garden Companion for Planting Bulbs, Pruning Hedges and Growing Fresh Herbs'
by Dr Owen Pratchard

I would like a bold, stand out cover. Contemporary. I would like to avoid stereotypical images of people looking anxious or worried. I would like the design to be more uplifting and hopeful, rather than focusing on the negative aspect of anxiety, but avoiding cliched photos of people raising their hands in the air, smiling and jumping etc. The cover should appeal to both men and women.

Trim size of book cover (for BindWell) is 5.25" x 8" back and front with a spine size of 0.477 inches
Updates

Reason: I have decided to extend the deadline by 1 more day, not because I am unhappy with the quality of the designs, but because a few designers have contacted me to explain they have had technical difficulties when submitting their files. Thanks everyone for the hard work and great designs.

Target Market(s)

Males and females (16+) who struggle with social anxiety and shyness

Industry/Entity Type

Social

Font styles to use
Serif

Requirements
Must have
• Bold cover that is modern and contemporary. For example, I like these covers:
• http://lnkvo.test/7kTq3Wm
• http://lnkvo.test/9gHw5Ze
• http://lnkvo.test/4nVy8Kb
• http://lnkvo.test/6jFu2Xo
• http://lnkvo.test/3mEs9Lt
• http://lnkvo.test/8hGz4Nd
• http://lnkvo.test/5bJk7Pv
Nice to have
• Open to abstract designs.
Should not have
• No stereotypical pictures of people who look anxious or worried. Avoid cliched photos of people raising their hands in the air, smiling and jumping etc.

```html
<!DOCTYPE html>
<html lang="en">
<head>
<meta charset="utf-8">
<title>Lanterns Along the Winding Quay – Book Cover</title>
<link rel="stylesheet" href="https://fonts.googleapis.com/css2?family=Jost:wght@300;400;500;700&display=swap">
<style>
  :root {
    --stage: #dcdcdc;
    --paper: #ffffff;
    --ink: #111111;
    --accent-red: #a3171b;
    --art-warm: #f3a24a;
    --art-mid: #e48ad6;
    --art-cool: #8a68cc;
  }
  * { box-sizing: border-box; margin: 0; padding: 0; }
  html, body {
    width: 1200px; height: 900px; overflow: hidden;
    background: var(--stage);
    font-family: "Jost", "Futura", sans-serif;
  }
  .cover {
    position: absolute; left: 337px; top: 0;
    width: 636px; height: 900px;
    background: var(--paper);
    overflow: hidden;
  }
  .cover__author {
    position: absolute; top: 58px; left: 0; width: 100%;
    text-align: center;
    font-size: 32px; font-weight: 500;
    letter-spacing: 0.42em;
    padding-left: 0.42em;
    color: var(--ink);
  }
  .cover__art {
    position: absolute; left: 14px; top: 132px;
    width: 620px; height: 620px; border-radius: 50%;
    background: linear-gradient(160deg, var(--art-warm) 0%, var(--art-mid) 55%, var(--art-cool) 100%);
    opacity: 0.85;
  }
  .cover__badge {
    position: absolute; left: 116px; top: 245px;
    width: 410px; height: 410px; border-radius: 50%;
    background: var(--paper);
    display: flex; flex-direction: column; align-items: center; justify-content: center;
    text-align: center;
  }
  .title { font-weight: 300; color: var(--ink); line-height: 0.98; }
  .title__lead {
    display: block;
    font-size: 30px; font-weight: 700;
    letter-spacing: 0.24em; padding-left: 0.24em;
    color: var(--accent-red);
    margin-bottom: 6px;
  }
  .title__line { display: block; font-size: 58px; }
  .cover__subtitle {
    position: absolute; left: 0; top: 796px; width: 100%;
    text-align: center;
    font-size: 20px; font-weight: 400; line-height: 1.15;
    color: var(--ink);
  }
</style>
</head>
<body>
  <main class="cover">
    <p class="cover__author">DR OWEN PRATCHARD</p>
    <div class="cover__art" role="img" aria-label="Abstract rainbow watercolour wash surrounding the title"></div>
    <div class="cover__badge">
      <h1 class="title">
        <span class="title__lead">LANTERNS</span>
        <span class="title__line">ALONG THE</span>
        <span class="title__line">WINDING</span>
        <span class="title__line">QUAY</span>
      </h1>
    </div>
    <p class="cover__subtitle">A Practical Seasonal Garden Companion for Planting Bulbs,<br>Pruning Hedges and Growing Fresh Herbs</p>
  </main>
</body>
</html>
```